Laser Tattoo Removal Business Cards

We are looking for a professional business card design for a laser tattoo removal business. Ideally looking for a black business card design. The name of the business is Brightline Tattoo Removal. We place our cards at local tattoo shops so we ideally are looking for something trendy/edgy to draw both male and female clientele in.

Target Market(s)

Male/Female ages 18-60

Contact Information for Business Card

black background ideally.. hoping to stay within greys, whites and black

Font styles to use
Serif
Sans Serif

Colors
121212
a9a9a9
5c5c5c
f5f5f5
ffffff
7f7f7f
606060
848484
9d9d9d

Requirements
Must have
• Employee Info:
• Melissa Thornbury
• Chief Executive Offer
• m: 919.537.2846
• w: 919.362.4178
• f: 919.685.3907
• mthornbury@brightlinetattooremoval.example
• Address:
• 4615 Oakmere Pkwy, Suite 210
• Raleigh, NC 27654
• Website:
• www.brightlinetattooremoval.example
Nice to have
• Myabe business name on back or logo on back and employee info on the front

```html
<!DOCTYPE html>
<html lang="en">
<head>
<meta charset="utf-8">
<title>Brightline Tattoo Removal – Business Card</title>
<link rel="stylesheet" href="https://fonts.googleapis.com/css2?family=Roboto:wght@400;500;700&display=swap">
<style>
  :root {
    --backdrop: #5c4a3a;
    --paper: #f5f5f5;
    --ink: #121212;
    --band-dark: #2a2a2a;
    --band-grey: #9d9d9d;
    --rule: #f5f5f5;
    --white: #ffffff;
    --card-back: #1b1c1e;
    --brand-ink: #2b2b2b;
  }
  * { margin: 0; padding: 0; box-sizing: border-box; }
  html, body {
    width: 1200px; height: 960px; overflow: hidden;
    background: var(--backdrop);
    font-family: "Roboto", Arial, sans-serif;
  }
  .canvas { position: relative; width: 1200px; height: 960px; }
  .card { position: absolute; width: 600px; height: 342px; overflow: hidden; }

  /* Front */
  .card--front { left: 322px; top: 108px; background: var(--paper); }
  .brand {
    position: absolute; left: 0; right: 0;
    text-align: center; text-transform: uppercase;
    font-weight: 500; letter-spacing: 3px;
  }
  .card--front .brand { top: 146px; font-size: 30px; color: var(--brand-ink); line-height: 1; transform: translateY(-50%); top: 114px; }
  .info-band {
    position: absolute; left: 0; top: 202px; width: 600px; height: 110px;
    background: var(--band-dark); color: var(--white);
  }
  .person { position: absolute; left: 24px; top: 16px; }
  .person__name { font-size: 21px; font-weight: 700; letter-spacing: 0.2px; line-height: 24px; }
  .person__title { font-size: 15px; font-weight: 500; line-height: 18px; }
  .address { position: absolute; left: 26px; top: 62px; font-size: 14px; line-height: 18px; }
  .contact {
    position: absolute; right: 31px; top: 23px;
    text-align: right; font-size: 14px; line-height: 19px;
  }
  .web-band {
    position: absolute; left: 0; top: 314px; width: 600px; height: 28px;
    background: var(--band-grey); border-top: 2px solid var(--rule);
    color: var(--white); font-size: 13px; letter-spacing: 3.2px;
    text-align: center; line-height: 25px;
  }

  /* Back */
  .card--back { left: 320px; top: 494px; background: var(--card-back); }
  .card--back .brand { top: 171px; transform: translateY(-50%); font-size: 30px; color: var(--white); line-height: 1; }
</style>
</head>
<body>
<main class="canvas">
  <section class="card card--front" aria-label="Business card front">
    <p class="brand">Brightline Tattoo Removal</p>
    <div class="info-band">
      <div class="person">
        <p class="person__name">MELISSA THORNBURY</p>
        <p class="person__title">Chief Executive Offer</p>
      </div>
      <address class="address" style="font-style:normal">
        4615 Oakmere Pkwy, Suite 210<br>
        Raleigh, NC 27654
      </address>
      <div class="contact">
        <p>(P) 919.362.4178</p>
        <p>(M) 919.537.2846</p>
        <p>(F) 919.685.3907</p>
        <p>mthornbury@brightlinetattooremoval.example</p>
      </div>
    </div>
    <p class="web-band">www.brightlinetattooremoval.example</p>
  </section>

  <section class="card card--back" aria-label="Business card back">
    <p class="brand">Brightline Tattoo Removal</p>
  </section>
</main>
</body>
</html>
```